I need podcast cover art that could also be incorporated into a website and social media accounts. I originally planned on calling the podcast "Bedside Bridgeway Lab" but need to change it to "Bedside Bridgeway Circle," and its purpose is to educate and inspire people on how we can deliver more affordable, higher quality health care in the United States. The target audience is anyone working in a healthcare related industry (doctors, nurses, healthcare insurers, policymakers involved in writing healthcare policy, etc...). The program will be well-researched and the tone will be upbeat. I will be interviewing experts in healthcare delivery including innovators who have come up with creative solutions to improving healthcare quality where they work. I want to keep the design very clean, simple, and modern looking. Thank you so much - I am looking forward to seeing your designs!

Target Market(s)

working professionals and students in healthcare-related fields

Industry/Entity Type

Health Care

Font styles to use
Sans Serif

Colors

Designer to choose colors to be used in the design.

Requirements
Must have
• very clean, simple and modern looking

```html
<!DOCTYPE html>
<html lang="en">
<head>
<meta charset="utf-8">
<title>Bedside Bridgeway Circle — Podcast Cover</title>
<link rel="stylesheet" href="https://fonts.googleapis.com/css2?family=Archivo+Narrow:wght@700&family=Roboto:wght@300&display=swap">
<style>
  :root {
    --salmon: #e8937e;
    --teal: #5dd8d5;
    --plum: #463f52;
    --yellow: #fcee21;
    --white: #ffffff;
  }
  html, body {
    margin: 0;
    padding: 0;
    width: 1200px;
    height: 1200px;
    overflow: hidden;
    background: var(--salmon);
  }
  .cover {
    display: block;
    width: 1200px;
    height: 1200px;
  }
  .cover__backdrop { fill: var(--salmon); }
  .cover__ring { fill: var(--teal); }
  .cover__orb { fill: var(--plum); }
  .title {
    font-family: "Archivo Narrow", "Arial Narrow", sans-serif;
    font-weight: 700;
    letter-spacing: -1px;
  }
  .title--white { fill: var(--white); font-size: 112px; }
  .title--accent { fill: var(--yellow); font-size: 140px; }
  .divider { stroke: var(--white); stroke-width: 2; }
  .tagline {
    font-family: "Roboto", "Helvetica Neue", sans-serif;
    font-weight: 300;
    font-size: 47px;
    fill: var(--white);
  }
</style>
</head>
<body>
<svg class="cover" viewBox="0 0 1200 1200" xmlns="http://www.w3.org/2000/svg" aria-labelledby="cover-title">
  <title id="cover-title">Bedside Bridgeway Circle — Discussions with Experts and Innovators</title>
  <rect class="cover__backdrop" width="1200" height="1200"/>
  <circle class="cover__ring" cx="920" cy="600" r="828"/>
  <circle class="cover__orb" cx="840" cy="600" r="308"/>

  <text class="title title--white" x="214" y="514">BEDSIDE</text>
  <text class="title title--accent" x="212" y="650">BRIDGEWAY</text>
  <text class="title title--white" x="214" y="760">CIRCLE</text>

  <line class="divider" x1="218" y1="801" x2="320" y2="801"/>

  <text class="tagline" x="214" y="888">Discussions with</text>
  <text class="tagline" x="214" y="956">Experts and Innovators</text>
</svg>
</body>
</html>
```